Adaptive GS Conversion & Enhancement B2B Site

We are looking to convert our current page to the adaptove Grid System (http://plinq.417.io/) and if there are some general enhancements, we would not complain :-)

We would expect delivery of static html for the following pages:
- home - http://www.bremvilo.com/
- detail - e.g. http://www.bremvilo.com/products/products.html
- help - http://www.bremvilo.com/help/te_reports/customer_approval.html

Our objective is to convert the page to a different system which is then based on the Adapt.js - from mobile.css to 2520.css

Target Market(s)

Business looking for Professional Services Project Management

Requirements
Must have
• Use of http://plinq.417.io/
Should not have
• Flash, or other frameworks (well jQuery is OK if it must be)

```html
<!DOCTYPE html>
<html lang="en">
<head>
<meta charset="utf-8">
<title>Bremvilo – Customer Approval</title>
<link href="https://fonts.googleapis.com/css2?family=PT+Sans:wght@400;700&family=Ubuntu:wght@400;500&display=swap" rel="stylesheet">
<style>
:root{
  --orange:#f8a90a;
  --orange-deep:#f39c00;
  --orange-line:#fbc357;
  --ink:#333;
  --ink-soft:#555;
  --grey-bg:#f3f3f3;
  --grey-line:#e4e4e4;
  --footer-dark:#3b3b3b;
  --badge-blue:#1f5f93;
  --white:#fff;
}
*{margin:0;padding:0;box-sizing:border-box}
html,body{width:937px;height:1200px;overflow:hidden;background:var(--white)}
.page{position:relative;width:1020px;height:1306px;transform:scale(.91863);transform-origin:0 0;font-family:"PT Sans",sans-serif;color:var(--ink)}
.header{position:absolute;left:0;top:0;width:1020px;height:122px;background:linear-gradient(#f0f0f0 0,#f0f0f0 6px,#fff 6px,#fafafa 122px)}
.search-tab{position:absolute;left:700px;top:6px;width:245px;height:33px;background:#e8e8e8;clip-path:polygon(0 0,100% 0,94% 100%,6% 100%)}
.search-field{position:absolute;left:722px;top:10px;width:198px;height:22px;border-radius:11px;background:var(--white);font-size:11px;color:#999;padding:4px 12px}
.search-field svg{position:absolute;right:9px;top:5px}
.brand{position:absolute;left:42px;top:46px;display:flex;align-items:center;gap:10px;font-family:"Ubuntu",sans-serif;font-weight:500;font-size:33px;color:#1d1d1d}
.brand-dot{width:32px;height:32px;border-radius:50%;background:var(--badge-blue)}
.main-nav{position:absolute;left:344px;top:74px;width:643px;height:47px;background:var(--orange);border-radius:6px 6px 0 0;display:flex;align-items:center;padding-left:5px}
.main-nav a{font-family:"Ubuntu",sans-serif;font-size:14.5px;color:var(--white);text-decoration:none;padding:0 21px;border-left:1px solid rgba(255,255,255,.6);line-height:16px}
.main-nav a:first-child{border-left:none}
.sidebar{position:absolute;left:22px;top:136px;width:281px;height:875px;background:var(--grey-bg);padding:10px 10px}
.side-nav{list-style:none;width:261px;height:855px;background:var(--orange);border-radius:6px;padding-top:32px;font-family:"Ubuntu",sans-serif;font-weight:500;font-size:13px;color:var(--white)}
.side-nav li{position:relative;height:28px;line-height:28px;margin-left:37px;width:185px;border-bottom:1px solid var(--orange-line);padding-left:18px}
.side-nav li:last-child{border-bottom:none}
.side-nav li.top{padding-left:18px}
.side-nav li.top::before{content:"";position:absolute;left:-10px;top:7px;width:14px;height:14px;border-radius:50%;background:var(--orange-deep);box-shadow:inset 0 0 0 1px #fcd27a}
.side-nav li.top::after{content:"";position:absolute;left:-4px;top:11px;border-left:4px solid var(--white);border-top:3px solid transparent;border-bottom:3px solid transparent}
.side-nav li.sub{padding-left:36px}
.side-nav li.sub::before{content:"";position:absolute;left:22px;top:11px;border-left:3px solid var(--white);border-top:3px solid transparent;border-bottom:3px solid transparent}
.side-nav li.plain{padding-left:18px}
.content{position:absolute;left:323px;top:158px;width:641px}
.content h1{font-family:"Ubuntu",sans-serif;font-weight:400;font-size:19.5px;color:#2b2b2b;margin-bottom:10px;letter-spacing:-.2px}
.content p{font-size:12.3px;line-height:18px;color:var(--ink-soft);text-align:justify;margin-bottom:28px}
.content p.tight{margin-bottom:5px}
.content p.close{margin-bottom:24px}
.content .comment-link{font-family:"Ubuntu",sans-serif;font-weight:500;font-size:12.5px;color:#333}
.footer{position:absolute;left:0;top:1027px;width:1020px;height:236px;background:var(--grey-bg)}
.footer-col{position:absolute;top:33px}
.footer-col h3{font-family:"Ubuntu",sans-serif;font-weight:400;font-size:14.5px;color:#222;margin-bottom:12px}
.footer-col ul{list-style:none;font-size:12px;color:var(--ink-soft)}
.footer-col li{height:25px}
.social-icons{display:flex;gap:10px;margin:6px 0 12px}
.social-icons span{width:27px;height:27px;border-radius:4px;background:#6d6d6d}
.social-links{font-size:11.5px;color:var(--ink-soft)}
.badge-accredited{position:absolute;left:801px;top:1061px;width:150px;height:57px;border-radius:5px;background:var(--badge-blue);box-shadow:0 0 0 1px #9db6cb}
.badge-partner{position:absolute;left:803px;top:1127px;width:201px;height:59px;background:var(--white);border:1px solid #e6e6e6}
.bottom-bar{position:absolute;left:0;top:1263px;width:1020px;height:43px;background:var(--footer-dark);color:#ddd;font-size:11px;padding:13px 44px}
</style>
</head>
<body>
<div class="page">
  <header class="header">
    <div class="search-tab"></div>
    <div class="search-field">Search here..
      <svg width="12" height="12" viewBox="0 0 12 12"><circle cx="5" cy="5" r="3.8" fill="none" stroke="#888" stroke-width="1.5"/><line x1="8" y1="8" x2="11" y2="11" stroke="#888" stroke-width="1.8"/></svg>
    </div>
    <div class="brand"><span class="brand-dot"></span>Bremvilo</div>
    <nav class="main-nav">
      <a>Home</a><a>Products</a><a>Services</a><a>Support</a><a>Blog</a><a>About Us</a><a>Contact Us</a>
    </nav>
  </header>

  <aside class="sidebar">
    <ul class="side-nav">
      <li class="top">Bremvilo Cloud Help</li>
      <li class="sub" style="padding-left:33px">Welcome</li>
      <li class="top">Opportunity Workbench</li>
      <li class="top">Time Expense Item Workbench</li>
      <li class="top">Workbench Setup</li>
      <li class="top">Using Time &amp; Expense</li>
      <li class="sub" style="padding-left:33px">Time &amp; Expense Items</li>
      <li class="sub">Time &amp; Expense Reports</li>
      <li class="sub">Customer Approval</li>
      <li class="sub">Payment Selection</li>
      <li class="sub">Bremvilo Timer</li>
      <li class="sub">Dashboards &amp; Reporting</li>
      <li class="top">Using Cloud Billing</li>
      <li class="sub">Invoices</li>
      <li class="top">Setup: Accounting</li>
      <li class="sub">Financial Organizations</li>
      <li class="sub">Financial Accounts</li>
      <li class="sub">Taxes</li>
      <li class="top">Setup: Time &amp; Expense</li>
      <li class="top">Setup: Billing</li>
      <li class="sub">Document Types</li>
      <li class="sub">Payment Terms</li>
      <li class="plain">Installation</li>
      <li class="sub">Remote Sites</li>
      <li class="sub">Email Processing</li>
      <li class="sub">Security &amp; Sharing</li>
      <li class="sub">Report Approval Process</li>
      <li class="sub">Page Layouts</li>
      <li class="sub">Alerts</li>
    </ul>
  </aside>

  <main class="content">
    <h1>CUSTOMER APPROVAL</h1>
    <p>There may be instances, generally when a customer is being billed for time and/or expenses, that it is desirable to receive a customer's approval of the time and expenses for a project or activity.&nbsp; This will help reduce the time it may take to receive payment from the customer.</p>
    <p>To use the customer approval first set up the necessary email service and ensure the Customer Approval button has been added to the T&amp;E Report page layout.&nbsp; This setup is generally done by the system administrator and details can be found in Installation.</p>
    <p>When a T&amp;E Report is in a completed status it can be submitted for customer approval.&nbsp; It is necessary to enter values in the Customer Approval section of the T&amp;E report.&nbsp; A valid Account and Contact must be entered and the contact must have a valid email address.&nbsp; This is the address the approval email is sent to.&nbsp; Select and Approval option of Time, Expense or Time &amp; Expense.&nbsp; The selection made will determine what information is included in the email text.</p>
    <p>The customer simply replies to the email with the text Approve or Reject in the first line of the response.&nbsp; Any comments can be added in the second line of the response.&nbsp; The approval status of the T&amp;E Report is updated as indicated and any comments are reflected in the Approval Comment field.&nbsp; Note that the Approval Status is separate for the Status field which is used for internal T&amp;E Report approval via the workflow.</p>
    <p class="tight">If the customer rejects the T&amp;E report, modifications can be made and the T&amp;E report can be re-submitted to the customer.</p>
    <p class="close">Customer approval is an optional step.&nbsp; Workflows can be designed to ensure that specific T&amp;E Reports are submitted to customers for approval provided the specific rules can be defined and replicated in the workflow environment.&nbsp; Refer to the workflow documentation in nimbusdesk.com or contact Bremvilo of additional assistance.</p>
    <div class="comment-link">Log in or register to post comments</div>
  </main>

  <footer class="footer">
    <div class="footer-col" style="left:42px">
      <h3>Company</h3>
      <ul><li>About Company</li><li>What We Do</li><li>Why We Are</li><li>Recent Blog</li><li>Services Offerd</li></ul>
    </div>
    <div class="footer-col" style="left:200px">
      <h3>Support</h3>
      <ul><li>Help</li><li>FAQ</li><li>Term of Use</li><li>Support</li><li>Contact Us</li></ul>
    </div>
    <div class="footer-col" style="left:343px">
      <h3>Contact Information</h3>
      <ul><li>Phone:+1 (650) 555-0148</li><li>418 Harbor Crest Drive,</li><li>Suite 210-47</li><li>Bayview City, CA 94011</li></ul>
    </div>
    <div class="footer-col" style="left:558px">
      <h3>Get In Touch</h3>
      <div class="social-icons"><span></span><span></span><span></span><span></span></div>
      <div class="social-links">Friendlane&nbsp; / &nbsp;Chirper&nbsp; / &nbsp;Viewreel&nbsp; / &nbsp;RSS</div>
    </div>
  </footer>
  <div class="badge-accredited" role="img" aria-label="Accreditation badge"></div>
  <div class="badge-partner" role="img" aria-label="Partner program badge"></div>
  <div class="bottom-bar">© 2012 Company Name.&nbsp; All right resreved</div>
</div>
</body>
</html>
```